Velk Partners Building Business Cards

We need a business card that reflects our business as "Solar Experts" in San Diego. Browse our website www.velkpartners.example our License needs to be displayed as "CSLB# 3867140" our phone number is (619) 555-0187

Save thousands on your electric bills and increase the value of your home while helping to protect the environment. Our solar installation experts will help you design the system that's right for you, using only the highest quality equipment that will look great and give you ideal performance. Our goal is to make you energy independent, and get your electric bill to 0.

Paul Osterby
(619) 555-0187
paul@velkpartners.example

Target Market(s)

Home owners in san diego looking for solar

Industry/Entity Type

Solar Energy

Contact Information for Business Card

Paul Osterby
(619) 555-0187
paul@velkpartners.example

Font styles to use
Other font styles liked:
• Use our logo font

Requirements
Must have
• License needs to be displayed as "CSLB# 3867140" our phone number is (619) 555-0187
Nice to have
• Real images of rooftop home solar in san diego
Should not have
• our business address

```html
<!DOCTYPE html>
<html lang="en">
<head>
<meta charset="utf-8">
<title>Velk Partners Building – Business Card</title>
<link href="https://fonts.googleapis.com/css2?family=Lato:wght@400;700;900&family=Roboto:wght@400&display=swap" rel="stylesheet">
<style>
  :root {
    --navy: #1b4580;
    --sun: #f6a821;
    --white: #ffffff;
    --backdrop: #e6e6e4;
    --divider: #c9a24a;
  }
  * { box-sizing: border-box; margin: 0; padding: 0; }
  html, body { width: 1200px; height: 1000px; overflow: hidden; }
  body { background: var(--backdrop); position: relative; font-family: "Lato", sans-serif; }

  .card {
    position: absolute;
    left: 316px;
    width: 561px;
    height: 320px;
    background: var(--white);
    border-radius: 24px;
    overflow: hidden;
    box-shadow: 0 3px 8px rgba(0,0,0,0.18);
  }
  .card--front { top: 172px; }
  .card--back { top: 536px; }

  .wordmark {
    position: absolute;
    display: flex;
    align-items: center;
    gap: 12px;
    white-space: nowrap;
  }
  .wordmark__dot {
    width: 30px; height: 30px;
    border-radius: 50%;
    background: var(--sun);
    flex: none;
  }
  .wordmark__name {
    font-family: "Lato", sans-serif;
    font-weight: 900;
    font-size: 40px;
    letter-spacing: -0.5px;
    color: var(--navy);
  }
  .card--front .wordmark { left: 40px; top: 52px; }
  .card--back .wordmark { left: 40px; top: 118px; }

  .contact-band {
    position: absolute;
    left: 0; top: 168px;
    width: 100%; height: 152px;
    background: var(--navy);
  }
  .holder-name {
    position: absolute;
    left: 38px; top: 64px;
    font-weight: 700;
    font-size: 26px;
    letter-spacing: 0.2px;
    color: var(--white);
  }
  .holder-name__last { color: var(--sun); }
  .band-divider {
    position: absolute;
    left: 271px; top: 52px;
    width: 1px; height: 56px;
    background: var(--divider);
  }
  .contact-list {
    position: absolute;
    left: 296px; top: 48px;
    list-style: none;
    font-family: "Roboto", sans-serif;
    font-size: 14px;
    color: var(--white);
  }
  .contact-list li {
    display: flex; align-items: center; gap: 12px;
    height: 20.5px;
  }
  .contact-list svg { width: 13px; height: 13px; flex: none; }
  .contact-list .accent { color: var(--sun); }

  .license-band {
    position: absolute;
    left: 0; top: 284px;
    width: 100%; height: 36px;
    background: var(--navy);
    border-top: 3px solid var(--sun);
    color: var(--white);
    font-size: 13px;
    text-align: center;
    line-height: 32px;
  }
</style>
</head>
<body>

  <section class="card card--front">
    <div class="wordmark">
      <span class="wordmark__dot"></span>
      <span class="wordmark__name">Velk Partners Building Inc</span>
    </div>
    <div class="contact-band">
      <p class="holder-name">PAUL <span class="holder-name__last">OSTERBY</span></p>
      <span class="band-divider"></span>
      <ul class="contact-list">
        <li>
          <svg viewBox="0 0 16 16" aria-hidden="true"><path fill="#fff" d="M3.6 1.2 6 3.6 4.7 5.6c.9 2 2.6 3.7 4.6 4.6l2-1.3 2.4 2.4-1.5 2.4C6.7 13.6 1.4 8.3 1.2 2.7z"/></svg>
          (619) 555-0187
        </li>
        <li>
          <svg viewBox="0 0 16 16" aria-hidden="true"><rect x="1" y="3" width="14" height="10" fill="none" stroke="#fff" stroke-width="1.3"/><path d="M1 3.5 8 9l7-5.5" fill="none" stroke="#fff" stroke-width="1.3"/></svg>
          paul@velkpartners.example
        </li>
        <li>
          <svg viewBox="0 0 16 16" aria-hidden="true"><g fill="none" stroke="#fff" stroke-width="1.2"><circle cx="8" cy="8" r="6.5"/><ellipse cx="8" cy="8" rx="3" ry="6.5"/><path d="M1.5 8h13M2.5 4.8h11M2.5 11.2h11"/></g></svg>
          <span>www.<span class="accent">velkpartners</span>.example</span>
        </li>
      </ul>
    </div>
  </section>

  <section class="card card--back">
    <div class="wordmark">
      <span class="wordmark__dot"></span>
      <span class="wordmark__name">Velk Partners Building Inc</span>
    </div>
    <div class="license-band">License-"CSLB# 3867140"</div>
  </section>

</body>
</html>
```